brightwell - Property Management DL Card

I am after a savvy designer to cut through junk mail! so many real estate agents use flyers to promote themselves and their business and usually sales. We are a property management firm (residential) and we want to represent landlords that have existing investment properties and need a quality agent to represent them. Can you help?
DL size, will be printed and delivered to mailboxes. For a look at our website go to www.brightwellrs.com.au. Keep it simple and clutter free.
it is to be double sided - with one side to be simple and clear - just our website, logo and telephone number on the back.
attached is our logo and our telephone number is 1300 48 92 16
the above are 2 essential elements to be included + our email address: admin@brightwellrs.com.au
also attached are our transparent price list

Target Market(s)
property investors,
people that manage properties themselves
Industry/Entity Type
Property Management
- arial
Look and feel

```html
<!DOCTYPE html>
<html lang="en">
<head>
<meta charset="utf-8">
<title>brightwell – Property Management DL Card</title>
<link rel="stylesheet" href="https://fonts.googleapis.com/css2?family=Open+Sans:wght@300;400;600;700&display=swap">
<style>
  :root {
    --page-bg: #d6d6d6;
    --card-frame: #bcb6aa;
    --card-back: #b2aa9a;
    --panel-white: #ffffff;
    --accent-orange: #ec7a22;
    --text-dark: #2b2b2b;
    --text-brown: #4a4036;
    --bullet-grey: #9a9a9a;
    --band-black: #111111;
  }
  * { box-sizing: border-box; margin: 0; padding: 0; }
  html, body { width: 1200px; height: 1200px; overflow: hidden; }
  body {
    background: var(--page-bg);
    font-family: "Open Sans", Arial, sans-serif;
    position: relative;
  }
  .card {
    position: absolute;
    left: 121px;
    width: 1000px;
    height: 500px;
  }
  /* Front */
  .card--front { top: 56px; background: var(--card-frame); }
  .front-photo {
    position: absolute;
    left: 0; top: 0;
    width: 668px; height: 500px;
    background:
      linear-gradient(180deg, rgba(235,232,228,0.9) 0%, rgba(205,195,185,0.2) 40%, rgba(60,60,60,0.5) 100%),
      linear-gradient(90deg, #3a3a3a 0%, #d9d4cc 35%, #e8c9a8 55%, #bdb5ab 75%, #3a3a3a 100%);
  }
  .front-photo-frame {
    position: absolute;
    left: 0; top: 0;
    width: 668px; height: 500px;
    border: solid rgba(190,182,170,0.55);
    border-width: 23px 0 23px 23px;
  }
  .front-panel {
    position: absolute;
    left: 668px; top: 23px;
    width: 309px; height: 454px;
    background: var(--panel-white);
  }
  .headline-band {
    position: absolute;
    left: 438px; top: 116px;
    width: 532px; height: 27px;
    background: linear-gradient(90deg, rgba(236,122,34,0) 0%, var(--accent-orange) 20%, var(--accent-orange) 80%, rgba(236,122,34,0.15) 100%);
  }
  .headline {
    position: absolute;
    left: 549px; top: 116px;
    font-size: 20px; line-height: 27px;
    font-weight: 600;
    color: #fff;
    white-space: nowrap;
  }
  .benefits {
    position: absolute;
    left: 697px; top: 156px;
    list-style: none;
    font-size: 16.5px;
    line-height: 21.5px;
    color: var(--text-dark);
  }
  .benefits li { position: relative; padding-left: 16px; }
  .benefits li::before {
    content: "";
    position: absolute;
    left: 1px; top: 7px;
    width: 7px; height: 7px;
    background: var(--bullet-grey);
    transform: rotate(45deg);
  }
  .brand-front {
    position: absolute;
    left: 749px; top: 388px;
    font-size: 40px; font-weight: 300;
    letter-spacing: -0.5px;
    color: var(--text-dark);
  }
  /* Back */
  .card--back { top: 638px; background: var(--card-back); }
  .brand-band {
    position: absolute;
    left: 37px; top: 51px;
    width: 362px; height: 69px;
    background: linear-gradient(90deg, rgba(17,17,17,0) 0%, var(--band-black) 22%, var(--band-black) 75%, rgba(17,17,17,0) 100%);
  }
  .brand-back {
    position: absolute;
    left: 0; top: 0;
    width: 100%;
    text-align: center;
    font-size: 38px; line-height: 69px; font-weight: 300;
    color: #fff;
  }
  .contact {
    position: absolute;
    left: 555px; top: 380px;
    padding-left: 20px;
    border-left: 2px solid var(--text-brown);
    color: var(--text-brown);
    font-size: 18px;
    line-height: 24px;
    letter-spacing: 0.6px;
  }
  .contact-call { font-weight: 400; }
  .contact-call .label { font-size: 17px; letter-spacing: 0.8px; }
  .contact-call .phone { font-size: 23px; font-weight: 700; margin-left: 8px; letter-spacing: 0.8px; }
</style>
</head>
<body>
  <section class="card card--front" aria-label="Card front">
    <div class="front-photo" role="img" aria-label="Photo of a bright modern living room with white sofas, dark rug and floor-to-ceiling windows at sunset"></div>
    <div class="front-photo-frame"></div>
    <div class="front-panel"></div>
    <div class="headline-band"></div>
    <h1 class="headline">Property Management specialists</h1>
    <ul class="benefits">
      <li>Excellent communication</li>
      <li>No hidden extras</li>
      <li>Minimal vacancy</li>
      <li>The best rent return</li>
    </ul>
    <div class="brand-front">brightwell</div>
  </section>

  <section class="card card--back" aria-label="Card back">
    <div class="brand-band"><div class="brand-back">brightwell</div></div>
    <address class="contact" style="font-style: normal;">
      <div class="contact-call"><span class="label">CALL TODAY!</span><span class="phone">1300 48 92 16</span></div>
      <div>PO Box B527, Harbour South NSW, 1290</div>
      <div>admin@brightwellrs.com.au</div>
    </address>
  </section>
</body>
</html>
```